Pull Up Banner - Recruitment Company

We would like a design for a pull up banner.

For context: we are a recruitment business. We specialise in helping people in healthcare industry to find jobs in Australia.

I have come up with several ideas and text for the banner. Feel free to use the following as you see appropriate:

- Our logo (see attached)
- 'Healthcare Recruitment Agency'
- Some sort of imagine / cartoon of medical professionals (ie. doctor, nurse, physiotherapist, speech pathologist). A cartoon is more friendly than committing to a photo
- 'Empowering your next career move'
- 'Discover tailored opportunities based on your career preferences'
- Dot points (allied health, nursing, medical imaging)
- Contact info at the bottom including our website (www.quellastaffing.com.au, our Instagram handle @quellastaffing, Mobile: XXXX XXX XXX. The title section for contact information could be 'Get in touch:'

Feel free to submit a couple of designs and we can merge aspects that look good on your designs and find the perfect fit.
Thank you
Updates

Hello,

Thank you for your initial submissions to this project. I appreciate the time you've invested.

After reviewing the first attempt, I'd like to share some feedback and initial observations:

- Professionalism and engagement: Is the overall appearance of the banner professional? It's crucial that we have a high-quality design as this will represent our business.

- Image selection: The image (whether cartoon or real people) appears quite generic. Please consider submitting the banner with a few different photos in the middle for us to choose from. Ensure the image is a good fit and not simply a generic stock photo.

- Contact section: Kindly remove the phone number; we no longer wish to include it on the banner. Instead, please include our website (www.quellastaffing.com.au) and Instagram handle (@quellastaffing).

- Color scheme: White, black, and red/pink are preferred, or alternatively, blue. However, please avoid incorporating too many different colors as it may detract from the professional appearance.

We will be printing the design on a banner and require it to look professional and engaging.

Thank you once again for your submissions. I hope the feedback provided above is helpful.

Warm regards,

Target Market(s)

Allied Health Australia

Font styles to use
Serif

Colors
0054AA
0677BA
7BADD7
CADEEF
E8F1F8
0094D4
00A9DD
6FCCEA
C7EBF8
E9F6FB
EB3D1F
EC4F4E
F09395
F8D3D4
FCEDEE

```html
<!DOCTYPE html>
<html lang="en">
<head>
<meta charset="utf-8">
<title>Quella Staffing – Pull Up Banner</title>
<link rel="stylesheet" href="https://fonts.googleapis.com/css2?family=Poppins:wght@300;500;600;700;800&family=Roboto+Condensed:wght@700&family=Oswald:wght@500&display=swap">
<style>
  :root {
    --pink: #F09395;
    --pink-strong: #EC6F70;
    --pink-soft: #F8C9CA;
    --pink-pale: #FCEDEE;
    --coral: #F5775F;
    --slate: #2F4A55;
    --teal: #2A9D9A;
    --sky: #C7EBF8;
    --navy: #0E1B2B;
    --black: #000000;
    --white: #FFFFFF;
    --grey-soft: #E6E6E6;
  }
  * { margin: 0; padding: 0; box-sizing: border-box; }
  html, body { width: 1200px; height: 2774px; overflow: hidden; background: var(--white); }
  .banner { position: relative; width: 1200px; height: 2774px; background: var(--white); overflow: hidden; font-family: "Poppins", sans-serif; color: var(--navy); }

  .hero-illustration {
    position: absolute; left: 96px; top: 140px; width: 992px; height: 930px;
    border-radius: 28px;
    background:
      radial-gradient(ellipse 30% 22% at 45% 22%, rgba(245,119,95,0.55) 0%, rgba(245,119,95,0) 100%),
      radial-gradient(ellipse 42% 10% at 55% 57%, rgba(245,119,95,0.75) 0%, rgba(245,119,95,0) 100%),
      radial-gradient(ellipse 50% 8% at 56% 66%, rgba(47,74,85,0.85) 0%, rgba(47,74,85,0) 100%),
      radial-gradient(ellipse 18% 26% at 72% 30%, rgba(200,200,200,0.7) 0%, rgba(200,200,200,0) 100%),
      linear-gradient(180deg, #F1F1F1 0%, #F6EDEA 55%, #FFFFFF 100%);
  }
  .hero-swoosh { position: absolute; left: 30px; top: 880px; width: 1060px; height: 300px; }

  .tagline-badge {
    position: absolute; left: 96px; top: 812px; width: 404px; height: 404px;
    border-radius: 50%; background: var(--pink-soft);
    display: flex; flex-direction: column; align-items: center; justify-content: center;
    text-align: center;
  }
  .tagline-badge .lead { font-family: "Oswald", sans-serif; font-weight: 500; font-size: 58px; line-height: 1; color: var(--pink-strong); letter-spacing: -0.5px; }
  .tagline-badge .rest { font-weight: 600; font-size: 50px; line-height: 1.1; color: var(--navy); }

  .brand-name {
    position: absolute; left: 0; width: 1200px; top: 1290px; text-align: center;
    font-weight: 800; font-size: 70px; letter-spacing: 5px; color: var(--black); line-height: 1;
  }

  .headline-primary {
    position: absolute; left: 0; width: 1200px; top: 1425px; text-align: center;
    font-weight: 700; font-size: 170px; line-height: 1; color: var(--pink); letter-spacing: -2px;
  }
  .headline-secondary {
    position: absolute; left: 0; width: 1200px; top: 1600px; text-align: center;
    font-family: "Roboto Condensed", sans-serif; font-weight: 700; font-size: 132px; line-height: 1;
    color: var(--navy); letter-spacing: -2px;
  }
  .intro {
    position: absolute; left: 0; width: 1200px; top: 1765px; text-align: center;
    font-weight: 500; font-size: 52px; line-height: 66px; color: var(--navy);
  }

  .specialties { position: absolute; left: 92px; top: 1997px; width: 1016px; height: 292px; display: flex; justify-content: space-between; }
  .specialty { width: 318px; height: 292px; border: 3px solid var(--pink-pale); border-radius: 14px; overflow: hidden; display: flex; flex-direction: column; background: var(--white); }
  .specialty-art { flex: 1; }
  .specialty-art.allied {
    background:
      radial-gradient(circle at 42% 32%, rgba(214,40,80,0.75) 0%, rgba(214,40,80,0) 28%),
      radial-gradient(ellipse 30% 45% at 75% 60%, rgba(6,119,186,0.55) 0%, rgba(6,119,186,0) 100%),
      radial-gradient(ellipse 30% 40% at 28% 70%, rgba(42,157,154,0.45) 0%, rgba(42,157,154,0) 100%),
      linear-gradient(180deg, #FFFFFF, #F1F1F1);
  }
  .specialty-art.nursing {
    background:
      radial-gradient(ellipse 22% 55% at 38% 60%, rgba(42,157,154,0.8) 0%, rgba(42,157,154,0) 100%),
      radial-gradient(ellipse 22% 55% at 62% 60%, rgba(0,84,170,0.55) 0%, rgba(0,84,170,0) 100%),
      linear-gradient(160deg, #9FDDF4, #E9F6FB);
  }
  .specialty-art.imaging {
    background:
      radial-gradient(circle at 62% 52%, rgba(0,169,221,0.7) 0%, rgba(0,169,221,0) 30%),
      radial-gradient(ellipse 20% 30% at 22% 72%, rgba(120,70,40,0.5) 0%, rgba(120,70,40,0) 100%),
      linear-gradient(180deg, #C9CFD6, #EEF1F4);
  }
  .specialty-label { height: 56px; background: var(--pink-soft); font-weight: 500; font-size: 34px; line-height: 56px; text-align: center; color: var(--navy); }

  .contact-heading {
    position: absolute; left: 0; width: 1200px; top: 2345px; text-align: center;
    font-weight: 700; font-size: 76px; line-height: 1; color: var(--black);
  }
  .contact-heading .accent { color: var(--pink-strong); }

  .footer-band { position: absolute; left: 0; top: 2500px; width: 1200px; height: 274px; background: var(--black); }

  .website-pill {
    position: absolute; left: 100px; top: 2456px; width: 988px; height: 110px;
    border-radius: 55px; background: var(--white); padding: 8px;
  }
  .website-pill span {
    display: block; width: 100%; height: 100%; border-radius: 47px; background: var(--pink-soft);
    text-align: center; font-weight: 700; font-size: 50px; line-height: 94px; letter-spacing: 3px; color: var(--black);
  }

  .social {
    position: absolute; left: 0; width: 1200px; top: 2608px; text-align: center;
    font-weight: 300; font-size: 50px; line-height: 64px; color: var(--white);
  }
  .social .dot { display: inline-block; width: 34px; height: 34px; border-radius: 50%; background: var(--pink-strong); vertical-align: -2px; margin: 0 14px 0 18px; }
  .social .handle { font-weight: 500; }
</style>
</head>
<body>
<div class="banner">
  <div class="hero-illustration" role="img" aria-label="Illustration of a physiotherapist fitting a knee brace on a patient lying on a treatment table, with a knee joint diagram and a potted plant"></div>
  <svg class="hero-swoosh" viewBox="0 0 1060 300" aria-hidden="true">
    <path d="M0 290 Q 60 250 130 240 L 140 255 Z" fill="#F8C9CA"/>
    <path d="M420 150 C 560 70, 700 290, 1020 250 C 760 330, 560 210, 420 220 Z" fill="#F8C9CA"/>
  </svg>

  <div class="tagline-badge">
    <div class="lead">EMPOWERING</div>
    <div class="rest">YOUR NEXT<br>CAREER<br>MOVE</div>
  </div>

  <div class="brand-name">QUELLA STAFFING</div>

  <h1 class="headline-primary">Healthcare</h1>
  <h2 class="headline-secondary">Recruitment Agency</h2>
  <p class="intro">Discover tailored opportunities<br>based on your career preferences</p>

  <div class="specialties">
    <div class="specialty">
      <div class="specialty-art allied" role="img" aria-label="Illustration of a carer with a patient in a wheelchair and a heart symbol"></div>
      <div class="specialty-label">Allied health</div>
    </div>
    <div class="specialty">
      <div class="specialty-art nursing" role="img" aria-label="Illustration of a nurse and a doctor reviewing a tablet"></div>
      <div class="specialty-label">Nursing</div>
    </div>
    <div class="specialty">
      <div class="specialty-art imaging" role="img" aria-label="Illustration of a technician at an MRI scanner"></div>
      <div class="specialty-label">Medical imaging</div>
    </div>
  </div>

  <div class="contact-heading"><span class="accent">GET IN</span> TOUCH</div>

  <div class="footer-band"></div>
  <div class="website-pill"><span>www.quellastaffing.com.au</span></div>
  <p class="social">Follow us at<span class="dot"></span><span class="handle">@quellastaffing</span></p>
</div>
</body>
</html>
```